MRT Property - Business Cards

Looking for a business card & general letterhead, signage etc design for our new logo.

Colours:
000a20
0056a2
00b5ef
0088ce
68cef2

Fonts:
Poppins
Karla

Please keep look and feel of new brand - example in the zip package I sent.

```html
<!DOCTYPE html>
<html lang="en">
<head>
<meta charset="utf-8">
<title>MRT Property – Business Cards</title>
<link href="https://fonts.googleapis.com/css2?family=Poppins:wght@400;500;700;800&display=swap" rel="stylesheet">
<style>
  :root {
    --ink: #000a20;
    --navy: #0056a2;
    --cyan: #00b5ef;
    --blue: #0088ce;
    --sky: #68cef2;
    --paper: #ffffff;
    --backdrop: #c9c9c9;
    --text: #1c1c1c;
  }
  * { margin: 0; padding: 0; box-sizing: border-box; }
  html, body { width: 1200px; height: 900px; overflow: hidden; }
  body {
    background: var(--backdrop);
    font-family: "Poppins", sans-serif;
    position: relative;
  }
  .card {
    position: absolute;
    width: 600px;
    height: 340px;
    border-radius: 28px;
    overflow: hidden;
    box-shadow: 0 6px 18px rgba(0, 10, 32, 0.25);
  }
  /* Front */
  .card-front { left: 60px; top: 80px; }
  .front-pattern {
    position: absolute; inset: 0;
    background: linear-gradient(115deg, var(--sky) 0%, #3aa6e0 30%, var(--blue) 60%, #0072b8 100%);
  }
  .front-wordmark {
    position: absolute; inset: 0;
    display: flex; align-items: center; justify-content: center;
    color: var(--paper);
    font-weight: 800;
    font-size: 150px;
    letter-spacing: 4px;
  }
  /* Back */
  .card-back { left: 540px; top: 470px; background: var(--paper); }
  .back-wordmark {
    position: absolute; left: 56px; top: 118px;
    width: 270px;
    color: var(--navy);
    font-weight: 800;
    font-size: 84px;
    line-height: 1;
    letter-spacing: 2px;
  }
  .divider {
    position: absolute; left: 330px; top: 70px;
    width: 2px; height: 150px;
    background: var(--cyan);
  }
  .contact-block { position: absolute; left: 352px; top: 66px; }
  .person-name {
    color: var(--navy);
    font-weight: 800;
    font-size: 25px;
    line-height: 1.1;
  }
  .person-role {
    color: var(--text);
    font-size: 15px;
    margin-bottom: 16px;
  }
  .contact-list { list-style: none; }
  .contact-item {
    display: flex; align-items: center; gap: 8px;
    color: var(--text);
    font-size: 15px;
    line-height: 1.5;
  }
  .contact-icon { width: 14px; height: 14px; flex: none; }
  .address {
    position: absolute; left: 0; right: 0; bottom: 40px;
    text-align: center;
    color: var(--text);
    font-size: 17px;
  }
</style>
</head>
<body>
  <section class="card card-front">
    <div class="front-pattern" role="img" aria-label="Repeating pattern of sail shapes in shades of blue"></div>
    <div class="front-wordmark">MRT</div>
  </section>

  <section class="card card-back">
    <div class="back-wordmark">MRT</div>
    <div class="divider"></div>
    <div class="contact-block">
      <p class="person-name">DANIEL REEVE</p>
      <p class="person-role">Managing Director</p>
      <ul class="contact-list">
        <li class="contact-item">
          <svg class="contact-icon" viewBox="0 0 16 16"><path fill="#00b5ef" d="M3.5 1.5l2.5 0 1 3.5-1.8 1.2a8 8 0 0 0 4.6 4.6L11 9l3.5 1v2.5c0 1-1 2-2 2A11 11 0 0 1 1.5 3.5c0-1 1-2 2-2z"/></svg>
          123 456 789
        </li>
        <li class="contact-item">
          <svg class="contact-icon" viewBox="0 0 16 16"><rect x="1" y="3" width="14" height="10" rx="1.5" fill="#00b5ef"/><path d="M1.5 4l6.5 5 6.5-5" stroke="#fff" stroke-width="1.3" fill="none"/></svg>
          info@yourmail.com
        </li>
        <li class="contact-item">
          <svg class="contact-icon" viewBox="0 0 16 16"><circle cx="8" cy="8" r="7" fill="#00b5ef"/><path d="M1 8h14M8 1c-3 3-3 11 0 14M8 1c3 3 3 11 0 14" stroke="#fff" stroke-width="1" fill="none"/></svg>
          www.yourwebsite.com
        </li>
      </ul>
    </div>
    <p class="address">Your address, City State, Zip 1234</p>
  </section>
</body>
</html>
```